Fitness Equipment & Service

I want to make the card eye catching and fun. We are called Corvane Motion Limited and we are based in Wales. We sell, install and service all types of fitness equipment from Skipping ropes, right through the Dumbbells, Kettle bells and Barbells through to state of the art Treadmills, Running Machines and Strength Equipment. We also design and install changing room furniture and lockers.

TYPOGRAPHY
We would like to use Futrura. Futura has an appearance of efficiency and forwardness. The typeface is derived
from simple geometric forms (near-perfect circles, triangles and squares) and is based on strokes of
near-even weight, which are low in contrast. This is most visible in the almost perfectly round stroke of
the o, which is nonetheless slightly ovoid.
The lowercase has tall ascenders, which rise above the cap line. The uppercase
characters present proportions similar to those of classical Roman capitals.

TYPOGRAPHIC CONSIDERATIONS
No Strike though
No Horizontal Scaling
No Drop Shadows
No Effects
Never use less than 120% Leading

OUR CORPORATE COLOURS
BRAND GUIDELINES
We were thinking that our primary colour palette consists of the Acid Green (Pantone 382) and Process Black.

We work closely with tquarly Ltd and would like to include their name on the card somewhere. I have attached images of the other brands that we work with as an idea or the small icons I have included that illustrate what we do?. I have very kindly been given permission to use any of the images off the files that I have included below, so I hope these help. I will include these below. I would be open to suggestions if it made the card more striking Can you do it?
Updates

Hi All, Just wanted to add a few thoughts but you are the guys with the creative visions (thats why are here) We are based in Wales, UK and we would be open to lots of different ideas on a theme but must be eye catching, Bold and FUN. If you can or think that the Welsh or any dragon could be put in there then go for it (its not a must have) We have also added some ideas for colour but again its over to you!! GO FOR IT ! Thanks and look forward to your visions! Owen

Hi All, Just thought I would sen through the contact details that need to be on the card. (if you want to play around with icons instead of the wording twitter, Facebook, go for it): Corvane Motion Limited Owen Pritchard Managing Director Mob: +44 (0)7582 913 406 e-mail: sales@corvanemotion.co.uk Web: Corvanemotion.co.uk twitter: @motionLetterbin Facebook: Corvane Motion Limited

```html
<!DOCTYPE html>
<html lang="en">
<head>
<meta charset="utf-8">
<title>Corvane Motion Limited – Business Card</title>
<link href="https://fonts.googleapis.com/css2?family=Jost:wght@400;500;700&display=swap" rel="stylesheet">
<style>
  :root {
    --stage: #e9e9ec;
    --paper: #ffffff;
    --navy-deep: #14245a;
    --navy: #203a86;
    --navy-light: #3558b0;
    --ink-navy: #1a2658;
    --on-navy: #ffffff;
    --ring: rgba(255,255,255,0.55);
    --shadow: rgba(10,20,50,0.18);
  }
  * { box-sizing: border-box; margin: 0; padding: 0; }
  html, body { width: 1200px; height: 950px; overflow: hidden; }
  body {
    background: var(--stage);
    font-family: "Jost", "Helvetica Neue", Arial, sans-serif;
    display: flex;
    flex-direction: column;
    align-items: center;
    justify-content: center;
    gap: 30px;
  }
  .card {
    position: relative;
    width: 760px;
    height: 434px;
    border-radius: 4px;
    overflow: hidden;
    box-shadow: 0 6px 22px var(--shadow);
  }

  /* Back of card */
  .card--back {
    background: linear-gradient(135deg, var(--navy-light) 0%, var(--navy) 45%, var(--navy-deep) 100%);
  }
  .back-mark {
    position: absolute;
    left: 50%; top: 50%;
    width: 150px; height: 150px;
    margin: -95px 0 0 -75px;
    border-radius: 50%;
    background: radial-gradient(circle at 40% 35%, var(--navy-light), var(--navy-deep));
    border: 5px solid #c9ced9;
  }
  .back-web {
    position: absolute;
    left: 50%; top: 50%;
    margin: 70px 0 0 -10px;
    color: var(--on-navy);
    font-size: 16px;
    line-height: 1.3;
    letter-spacing: 1.5px;
    display: flex;
    align-items: center;
    gap: 8px;
  }
  .back-web::after {
    content: "";
    width: 70px; height: 1px;
    background: var(--ring);
  }

  /* Front of card */
  .card--front { background: var(--paper); }
  .brand {
    position: absolute;
    left: 56px; top: 70px;
    width: 280px;
    display: flex;
    flex-direction: column;
    align-items: flex-start;
    gap: 22px;
  }
  .brand__disc {
    width: 140px; height: 140px;
    margin-left: 40px;
    border-radius: 50%;
    background: radial-gradient(circle at 40% 35%, var(--navy-light), var(--navy-deep));
    border: 4px solid #c9ced9;
  }
  .brand__name {
    color: var(--ink-navy);
    font-weight: 700;
    font-size: 26px;
    line-height: 1.2;
    text-transform: uppercase;
    letter-spacing: 0.5px;
  }
  .contact-disc {
    position: absolute;
    left: 360px; top: -110px;
    width: 660px; height: 660px;
    border-radius: 50%;
    background: radial-gradient(circle at 30% 40%, var(--navy-light) 0%, var(--navy) 40%, var(--navy-deep) 80%);
    border: 3px solid var(--ring);
  }
  .contact {
    position: absolute;
    right: 36px; top: 74px;
    color: var(--on-navy);
    text-align: right;
  }
  .contact__name { font-size: 26px; font-weight: 700; line-height: 1.2; }
  .contact__role { font-size: 19px; line-height: 1.3; margin-bottom: 18px; }
  .contact__line {
    font-size: 17px;
    line-height: 1.45;
    display: flex;
    justify-content: flex-end;
    align-items: center;
    gap: 10px;
  }
  .contact__line--plain { padding-right: 26px; }
  .icon { width: 16px; height: 16px; flex: none; }
</style>
</head>
<body>

  <section class="card card--back" aria-label="Card back">
    <div class="back-mark"></div>
    <p class="back-web">corvanemotion.co.uk</p>
  </section>

  <section class="card card--front" aria-label="Card front">
    <div class="brand">
      <div class="brand__disc"></div>
      <p class="brand__name">Corvane Motion Limited</p>
    </div>

    <div class="contact-disc"></div>

    <div class="contact">
      <p class="contact__name">Owen Pritchard</p>
      <p class="contact__role">Managing Director</p>
      <p class="contact__line contact__line--plain">27 Castle Quay Road</p>
      <p class="contact__line contact__line--plain">Cardiff Bay, CF10 4PA</p>
      <p class="contact__line">+44 (0)7582 913 406
        <svg class="icon" viewBox="0 0 16 16"><rect x="4" y="1" width="8" height="14" rx="1.5" fill="none" stroke="#fff" stroke-width="1.6"/><circle cx="8" cy="12.3" r="0.9" fill="#fff"/></svg>
      </p>
      <p class="contact__line">sales@corvanemotion.co.uk
        <svg class="icon" viewBox="0 0 16 16"><rect x="1" y="3.5" width="14" height="9" fill="#fff"/><path d="M1 3.5 L8 9 L15 3.5" fill="none" stroke="#203a86" stroke-width="1.3"/></svg>
      </p>
      <p class="contact__line">Corvanemotion.co.uk
        <svg class="icon" viewBox="0 0 16 16"><circle cx="8" cy="8" r="6.5" fill="none" stroke="#fff" stroke-width="1.5"/><path d="M1.5 8 H14.5 M8 1.5 C5 5 5 11 8 14.5 M8 1.5 C11 5 11 11 8 14.5" fill="none" stroke="#fff" stroke-width="1.1"/></svg>
      </p>
      <p class="contact__line">@motionLetterbin
        <svg class="icon" viewBox="0 0 16 16"><rect x="1.5" y="1.5" width="13" height="13" rx="2" fill="#fff"/></svg>
      </p>
      <p class="contact__line">Corvane Motion Limited
        <svg class="icon" viewBox="0 0 16 16"><rect x="1.5" y="1.5" width="13" height="13" rx="2" fill="#fff"/></svg>
      </p>
    </div>
  </section>

</body>
</html>
```